Vernac Law Business cards and stationary design project

We are looking for a stationary design for business cards (double sided), 8x10, 5x7, and legal and standard envelopes.

We would like the design to match the logo that we have already.
Color palate preferred is Teal, White, grey and any others that will look good for a professional law firm.

We would like this statement: "RELATIONSHIPS. RESPECT. RESULT" to be on the back of the business cards and maybe on the stationary if it looks good.

Please see link to website for more information: www.vernac-law.example

Target Market(s)

Potential clients that need Attorney services.

Industry/Entity Type

Law Firm

Contact Information for Business Card

We would like the front and back to be two different colors. Current business cards are teal front, grey back and are a vertical design. We are open to options with colors.

Font styles to use
Serif

Colors
33a6d7
33b8a4
b9b9b9
5c5c5c

Requirements
Must have
• Logo supplied needs to go on the card and stationary.
• Match website color palate, www.vernac-law.example
• Be professional and not too wordy.
• Criminal Law, Civil Litigation, Personal Injury, Restraining Orders need to be on the card.
Nice to have
• RELATIONSHIPS. RESPECT. RESULTS. on the back of the card.
Should not have
• Not be too busy/wordy or too flashy.

```html
<!DOCTYPE html>
<html lang="en">
<head>
<meta charset="utf-8">
<title>Vernac Law – Business Card</title>
<link rel="stylesheet" href="https://fonts.googleapis.com/css2?family=Open+Sans:wght@400;600;700&display=swap">
<style>
  :root {
    --backdrop: #000000;
    --card-light: #f3f3f3;
    --card-teal: #0f8391;
    --teal-ink: #147f8c;
    --dark-ink: #1e1e1e;
    --white: #ffffff;
  }
  * { margin: 0; padding: 0; box-sizing: border-box; }
  html, body {
    width: 1200px; height: 900px; overflow: hidden;
    background: var(--backdrop);
    font-family: "Open Sans", Arial, sans-serif;
  }
  .canvas { position: relative; width: 1200px; height: 900px; }

  .card { position: absolute; top: 200px; width: 310px; height: 502px; }
  .card-front {
    left: 265px; background: var(--card-light);
    border-radius: 52px 0 52px 0;
  }
  .card-back {
    left: 641px; width: 309px; background: var(--card-teal);
    border-radius: 0 52px 0 52px; color: var(--white);
  }

  .brand-mark {
    position: absolute; left: 50%; top: 36px; transform: translateX(-50%);
    width: 70px; height: 70px; border-radius: 50%; background: var(--teal-ink);
  }
  .brand-name {
    position: absolute; left: 0; width: 100%; text-align: center;
    font-weight: 600; letter-spacing: 1px; text-transform: uppercase;
  }
  .card-front .brand-name { top: 140px; left: 22px; font-size: 31px; color: var(--teal-ink); }
  .card-back .brand-name { top: 74px; font-size: 29px; color: var(--white); }

  .contact { position: absolute; left: 27px; top: 303px; color: var(--dark-ink); }
  .contact-name { font-size: 18px; font-weight: 700; color: var(--teal-ink); line-height: 22px; }
  .contact-role { font-size: 13px; line-height: 18px; }
  .contact-address { margin-top: 12px; font-size: 13px; line-height: 15px; }
  .contact-list { margin-top: 13px; list-style: none; font-size: 13px; }
  .contact-list li { display: flex; align-items: center; height: 20.5px; }
  .contact-list svg { width: 10px; height: 10px; margin-right: 10px; fill: var(--teal-ink); }

  .practice-areas {
    position: absolute; left: 36px; top: 347px;
    font-size: 15px; font-weight: 600; line-height: 20.5px;
  }
  .tagline {
    position: absolute; left: 37px; top: 431px;
    font-size: 14.5px; font-weight: 700; letter-spacing: 0.1px;
  }
</style>
</head>
<body>
<main class="canvas">
  <section class="card card-front">
    <span class="brand-mark"></span>
    <p class="brand-name">Vernac Law</p>
    <div class="contact">
      <p class="contact-name">Daniel Mercer</p>
      <p class="contact-role">Managing Director</p>
      <p class="contact-address">12345, Address Goes Here<br>Country Name, 123456</p>
      <ul class="contact-list">
        <li><svg viewBox="0 0 10 10"><path d="M2 0.5 L3.6 2.6 L2.8 3.7 Q4 6 6.3 7.2 L7.4 6.4 L9.5 8 L8.4 9.5 Q1 8.5 0.5 1.6 Z"/></svg>(044)-456-7890</li>
        <li><svg viewBox="0 0 10 10"><path d="M2 0h5v3H2z M0 3.5h10v6H0z M2 5h2v1H2z M2 7h2v1H2z M6 5h2v3H6z"/></svg>123-456-7890</li>
        <li><svg viewBox="0 0 10 10"><path d="M0 1.5h10v1L5 6 0 2.5z M0 4l5 3.5L10 4v4.5H0z"/></svg>info@youremail.com</li>
        <li><svg viewBox="0 0 10 10"><circle cx="5" cy="5" r="4.8"/></svg>www.vernac-law.example</li>
      </ul>
    </div>
  </section>

  <section class="card card-back">
    <p class="brand-name">Vernac Law</p>
    <p class="practice-areas">Practice areas, Criminal Law<br>Civil Litigation/Personal Injury<br>Restraining Orders</p>
    <p class="tagline">RELATIONSHIPS. RESPECT. RESULT</p>
  </section>
</main>
</body>
</html>
```